Larkfield Ridge Management

I need a professional website. My current website is larkfieldridgemanagement.com and I hate it. It was created with some AI tool very quickly because I needed a site up and running with no advanced notice. I’m open to all designs .. I trust you, the professionals will deliver the results I’m anxiously awaiting! :)

```html
<!DOCTYPE html>
<html lang="en">
<head>
<meta charset="utf-8">
<title>Larkfield Ridge Management — Property Management</title>
<link rel="stylesheet" href="https://fonts.googleapis.com/css2?family=Montserrat:wght@400;500;600;700;800&family=Mulish:wght@400;500;600;700&display=swap">
<style>
:root{
  --navy:#1b2a4c;
  --navy-deep:#152240;
  --red:#c01d2e;
  --ink:#2a2f3a;
  --muted:#4a5060;
  --mist:#f1eff2;
  --line:#d9dbe2;
  --white:#ffffff;
}
*{box-sizing:border-box;margin:0;padding:0}
html,body{width:1200px;height:4922px;overflow:hidden}
body{position:relative;background:var(--white);font-family:"Mulish",sans-serif;color:var(--ink)}
.abs{position:absolute}
.heading{font-family:"Montserrat",sans-serif;color:var(--navy);text-transform:uppercase;letter-spacing:.5px;line-height:1.22}
.heading .light{font-weight:500;display:block}
.heading .bold{font-weight:800;display:block}
.heading .line{display:block;white-space:nowrap}
.heading .w-light{font-weight:500}
.heading .w-bold{font-weight:800}
.rule{width:56px;height:2px;background:var(--navy)}
.btn{display:inline-flex;align-items:center;justify-content:center;background:var(--red);color:var(--white);font-family:"Montserrat",sans-serif;font-weight:700;text-transform:uppercase;letter-spacing:.3px;text-decoration:none}
.body-copy{font-size:12.5px;line-height:19px;color:var(--muted)}

/* header */
.site-header{left:0;top:0;width:1200px;height:147px;background:var(--white)}
.brand{left:140px;top:20px;width:172px;height:150px;background:var(--white);display:flex;align-items:center;justify-content:center;text-align:center;z-index:5;clip-path:polygon(0 0,100% 0,100% 72%,50% 100%,0 72%)}
.brand span{font-family:"Montserrat",sans-serif;font-weight:800;color:var(--navy);font-size:19px;line-height:22px;text-transform:uppercase;padding-bottom:22px}
.phone-btn{left:623px;top:29px;width:183px;height:44px;border:1.5px solid var(--navy);display:flex;align-items:center;justify-content:center;gap:10px;font-family:"Montserrat",sans-serif;font-size:14px;font-weight:500;color:var(--navy)}
.top-cta{left:824px;top:29px;width:223px;height:44px;font-size:13px}
.main-nav{left:476px;top:94px;display:flex;gap:4px;list-style:none}
.main-nav li{font-family:"Montserrat",sans-serif;font-size:13px;font-weight:500;color:var(--navy);padding:8px 12px;text-transform:uppercase}
.main-nav li.active{background:var(--navy);color:var(--white)}

/* hero */
.hero{left:0;top:147px;width:1200px;height:570px;background:linear-gradient(90deg,#3a2a20 0%,#5b4332 30%,#6f6a66 52%,#a6a39c 75%,#c7c0b4 100%)}
.hero-shade{left:0;top:147px;width:700px;height:570px;background:linear-gradient(90deg,rgba(20,14,10,.55),rgba(20,14,10,0))}
.hero-title{left:157px;top:230px;color:var(--white);font-size:35px;line-height:41px}
.hero-title .light,.hero-title .bold{color:var(--white)}
.hero-title .mark{background:var(--red);padding:0 8px 0 0;display:inline-block}
.hero-cta{left:157px;top:543px;width:248px;height:52px;font-size:14px}
.hero-dots{left:554px;top:657px;display:flex;gap:14px}
.hero-dots i{width:11px;height:11px;border-radius:50%;background:var(--white);display:block}
.hero-dots i.on{background:var(--red)}
.hero-edge{left:0;top:630px}

/* trusted */
.trusted-shield{left:149px;top:793px;width:425px;height:370px}
.trusted-photo{left:165px;top:807px;width:393px;height:338px;background:linear-gradient(135deg,#2c3d66,#203258 60%,#1b2a4c);clip-path:polygon(0 0,100% 0,100% 72%,50% 100%,0 72%)}
.quad{position:absolute;width:196px;height:130px;display:flex;align-items:center;justify-content:center;text-align:center;color:var(--white);font-size:17px;line-height:23px;font-weight:500}
.trusted-title{left:627px;top:788px;font-size:26px}
.trusted-rule{left:627px;top:876px}
.trusted-copy{left:627px;top:907px;width:420px}
.trusted-copy p+p{margin-top:19px}
.trusted-cta{left:630px;top:1114px;width:118px;height:41px;font-size:11.5px}

/* services */
.services{left:0;top:1233px;width:1200px;height:841px;background:var(--mist)}
.services-title{left:0;top:1296px;width:1200px;text-align:center;font-size:26px}
.services-rule{left:572px;top:1366px}
.service{width:260px;text-align:center}
.service .badge{width:104px;height:90px;margin:0 auto;background:var(--navy);clip-path:polygon(0 0,100% 0,100% 70%,50% 100%,0 70%);display:flex;justify-content:center;padding-top:16px}
.service h3{margin-top:26px;font-family:"Montserrat",sans-serif;font-weight:700;font-size:14.5px;line-height:21px;color:var(--navy)}
.service p{margin-top:14px;font-size:12px;line-height:18px;color:var(--muted)}
.service .btn{margin-top:16px;width:106px;height:30px;font-size:11px}

/* benefits */
.benefits{left:0;top:2074px;width:1200px;height:691px;background:var(--navy)}
.benefits-notch{left:0;top:2073px}
.benefits-photo{left:147px;top:2221px;width:442px;height:479px;background:linear-gradient(150deg,#efe8dc,#cdbfa9 45%,#6b655f 85%);clip-path:polygon(0 0,100% 0,100% 72%,50% 100%,0 72%)}
.benefits-title{left:644px;top:2213px;font-size:26px;color:var(--white)}
.benefits-title .light,.benefits-title .bold{color:var(--white)}
.benefits-rule{left:646px;top:2304px;background:var(--white)}
.benefits-copy{left:646px;top:2333px;width:400px;color:#d5d9e3}
.benefits-list{left:646px;top:2454px;list-style:none}
.benefits-list li{font-size:12.5px;line-height:22.5px;color:#d5d9e3;padding-left:21px;position:relative}
.benefits-list li::before{content:"";position:absolute;left:2px;top:7px;border-left:6px solid var(--white);border-top:4.5px solid transparent;border-bottom:4.5px solid transparent}
.benefits-cta{left:650px;top:2666px;width:112px;height:40px;font-size:11.5px}

/* why choose */
.why-title{left:149px;top:2836px;font-size:27px;line-height:33px}
.why-list{left:149px;top:3038px;list-style:none}
.why-list li{display:flex;align-items:center;gap:18px;height:47px;font-family:"Montserrat",sans-serif;font-weight:600;font-size:15px;color:var(--navy)}
.why-list .dot{width:34px;height:34px;border-radius:50%;background:var(--navy);display:flex;align-items:center;justify-content:center}
.why-cta{left:151px;top:3346px;width:248px;height:52px;font-size:14px}
.why-photo{left:566px;top:2851px;width:481px;height:554px;background:linear-gradient(180deg,#e9e9ea,#dcdcde 45%,#c5c4c6);clip-path:polygon(0 0,100% 0,100% 72%,50% 100%,0 72%)}

/* delivering */
.delivering{left:0;top:3478px;width:1200px;height:491px;background:var(--mist)}
.delivering-photo{left:0;top:3478px;width:640px;height:491px;background:linear-gradient(90deg,#8c7a6a,#b8a48e 45%,#ddd5cb 80%,rgba(241,239,242,0) 100%)}
.delivering-title{left:634px;top:3539px;font-size:26px}
.delivering-rule{left:636px;top:3629px}
.delivering-copy{left:636px;top:3654px;width:410px}
.delivering-cta{left:633px;top:3854px;width:214px;height:49px;font-size:14px}

/* contact */
.contact-title{left:155px;top:4090px;font-size:26px;line-height:34px}
.contact-rule{left:156px;top:4205px}
.contact-copy{left:156px;top:4237px;width:368px}
.contact-cta{left:157px;top:4358px;width:152px;height:52px;font-size:14px}
.form-box{left:598px;top:4036px;width:449px;height:417px;background:var(--navy)}
.field{position:absolute;left:40px;width:373px;height:42px;background:var(--white);font-size:12.5px;color:#555;padding:13px 14px}
.submit{position:absolute;left:40px;top:341px;width:373px;height:52px;font-size:20px}
.hatch{position:absolute;width:60px;height:26px;background:repeating-linear-gradient(-55deg,var(--navy) 0 2px,transparent 2px 6px)}

/* footer */
.site-footer{left:0;top:4520px;width:1200px;height:402px;background:#efeef0}
.footer-brand{left:149px;top:4572px;width:200px;height:210px;background:var(--white);clip-path:polygon(0 0,100% 0,100% 72%,50% 100%,0 72%);display:flex;align-items:center;justify-content:center;text-align:center}
.footer-brand span{font-family:"Montserrat",sans-serif;font-weight:800;color:var(--navy);font-size:21px;line-height:25px;text-transform:uppercase;padding-bottom:30px}
.foot-h{font-family:"Montserrat",sans-serif;font-weight:700;font-size:14px;color:var(--navy);text-transform:uppercase}
.foot-col ul{list-style:none;margin-top:16px}
.foot-col li{font-size:11.5px;line-height:21.5px;color:var(--ink)}
.contact-row{display:flex;gap:14px;font-size:11.5px;line-height:17px;margin-bottom:20px}
.footer-rule{left:149px;top:4838px;width:898px;height:1px;background:var(--line)}
.follow{left:155px;top:4855px;display:flex;align-items:center;gap:6px;font-family:"Montserrat",sans-serif;font-weight:700;font-size:12px;color:var(--navy)}
.follow i{width:24px;height:24px;border-radius:50%;background:var(--navy);display:block}
.follow b{margin-right:10px}
.copyright{left:818px;top:4860px;font-size:11.5px;color:var(--ink)}
</style>
</head>
<body>

<!-- Header -->
<header class="abs site-header"></header>
<div class="abs brand"><span>Larkfield<br>Ridge<br>Management</span></div>
<div class="abs phone-btn">
  <svg width="18" height="18" viewBox="0 0 24 24" fill="none" stroke="#1b2a4c" stroke-width="1.8"><path d="M5 3h4l2 5-2.5 1.5a11 11 0 0 0 6 6L16 13l5 2v4a2 2 0 0 1-2 2A17 17 0 0 1 3 5a2 2 0 0 1 2-2z"/></svg>
  +1 555 014 2270
</div>
<a class="abs btn top-cta">Request a Consultation</a>
<ul class="abs main-nav">
  <li class="active">Home</li><li>About Us</li><li>Services</li><li>Industries</li><li>Resources</li><li>Contact Us</li>
</ul>

<!-- Hero -->
<div class="abs hero" role="img" aria-label="Photo of a property manager showing a smiling couple around a bright modern home interior"></div>
<div class="abs hero-shade"></div>
<h1 class="abs heading hero-title">
  <span class="light">Property</span>
  <span class="light">Management</span>
  <span class="bold">Solutions That</span>
  <span class="bold"><span class="mark">Protect, Optimize,</span></span>
  <span class="bold">And Grow Your</span>
  <span class="bold">Real Estate</span>
  <span class="bold">Investments</span>
</h1>
<a class="abs btn hero-cta">Request a Consultation</a>
<svg class="abs hero-edge" width="1200" height="90" viewBox="0 0 1200 90">
  <polygon points="0,20 600,88 1200,20 1200,90 0,90" fill="#fff"/>
  <polyline points="0,20 600,88 1200,20" fill="none" stroke="#1b2a4c" stroke-width="6"/>
</svg>
<div class="abs hero-dots"><i class="on"></i><i></i><i></i><i></i></div>

<!-- Trusted partner -->
<svg class="abs trusted-shield" viewBox="0 0 425 370">
  <polygon points="3,3 422,3 422,268 212,366 3,268" fill="none" stroke="#1b2a4c" stroke-width="6"/>
  <polygon points="422,-8 427,6 442,6 430,15 434,29 422,20 410,29 414,15 402,6 417,6" fill="#c01d2e" transform="translate(-2,10) scale(1.05)"/>
</svg>
<div class="abs trusted-photo" role="img" aria-label="Photo of a team meeting in an office, tinted navy">
  <div class="quad" style="left:0;top:0">Practical<br>Sensibility</div>
  <div class="quad" style="left:197px;top:0">Technological<br>Intelligence</div>
  <div class="quad" style="left:0;top:131px">Financial<br>Expertise</div>
  <div class="quad" style="left:197px;top:131px">Emotional<br>Awareness</div>
  <div style="position:absolute;left:196px;top:0;width:2px;height:262px;background:#fff"></div>
  <div style="position:absolute;left:0;top:130px;width:393px;height:2px;background:#fff"></div>
</div>
<h2 class="abs heading trusted-title"><span class="bold">Trusted Property</span><span class="light">Management Partner</span></h2>
<div class="abs rule trusted-rule"></div>
<div class="abs body-copy trusted-copy">
  <p>Managing a property requires expertise, attention to detail, and a proactive approach. Our property management specialists oversee every aspect of property operations to help owners improve asset performance, maintain high occupancy, and deliver exceptional tenant experiences.</p>
  <p>Whether managing a single investment property or an extensive portfolio, we develop customized management strategies that align with your financial objectives and long-term ownership goals.</p>
</div>
<a class="abs btn trusted-cta">Read More</a>

<!-- Services -->
<section class="abs services"></section>
<h2 class="abs heading services-title"><span class="w-light">Our </span><span class="w-bold">Property Management</span><span class="w-light"> Services</span></h2>
<div class="abs rule services-rule"></div>

<div class="abs service" style="left:138px;top:1430px">
  <div class="badge"><svg width="48" height="42" viewBox="0 0 48 42" fill="none" stroke="#fff" stroke-width="1.8"><path d="M4 20 24 5l20 15"/><path d="M9 17v22h30V17"/><rect x="20" y="27" width="8" height="12"/><rect x="13" y="21" width="6" height="5"/><rect x="29" y="21" width="6" height="5"/></svg></div>
  <h3>Residential Property<br>Management</h3>
  <p>Lorem ipsum dolor sit amet, consectetur adipiscing elit, sed do eiusmod tempor incididunt ut labore et dolore.</p>
  <a class="btn">Read More</a>
</div>
<div class="abs service" style="left:468px;top:1430px">
  <div class="badge"><svg width="48" height="48" viewBox="0 0 48 48" fill="none" stroke="#fff" stroke-width="1.8"><rect x="12" y="4" width="18" height="40"/><path d="M30 16h8v28"/><path d="M16 10h4M22 10h4M16 16h4M22 16h4M16 22h4M22 22h4M16 28h4M22 28h4"/><path d="M18 44v-8h6v8M8 44h34"/></svg></div>
  <h3>Commercial Property<br>Management</h3>
  <p>Lorem ipsum dolor sit amet, consectetur adipiscing elit, sed do eiusmod tempor incididunt ut labore et dolore.</p>
  <a class="btn">Read More</a>
</div>
<div class="abs service" style="left:801px;top:1430px">
  <div class="badge"><svg width="44" height="48" viewBox="0 0 44 48" fill="none" stroke="#fff" stroke-width="1.8"><path d="M8 4h20l8 8v30H8z"/><path d="M28 4v8h8M14 18h16M14 24h16M14 30h8"/><circle cx="32" cy="36" r="7"/><path d="m29 36 2 2 4-4"/></svg></div>
  <h3>Compliance &amp; Risk<br>Management</h3>
  <p>Lorem ipsum dolor sit amet, consectetur adipiscing elit, sed do eiusmod tempor incididunt ut labore et dolore.</p>
  <a class="btn">Read More</a>
</div>

<div class="abs service" style="left:138px;top:1777px">
  <div class="badge"><svg width="50" height="46" viewBox="0 0 50 46" fill="none" stroke="#fff" stroke-width="1.8"><path d="M15 16 25 7l10 9"/><path d="M18 14v12h14V14"/><path d="M25 17v6M23 18h3a1.5 1.5 0 0 1 0 3h-2a1.5 1.5 0 0 0 0 3h3"/><path d="M3 30l9-3 8 4 8 1a2 2 0 0 1 0 4h-7"/><path d="M47 30l-9-3-8 5M12 40l8 3h8l13-9"/></svg></div>
  <h3>Tenant Management</h3>
  <p>Lorem ipsum dolor sit amet, consectetur adipiscing elit, sed do eiusmod tempor incididunt ut labore et dolore.</p>
  <a class="btn">Read More</a>
</div>
<div class="abs service" style="left:468px;top:1777px">
  <div class="badge"><svg width="50" height="46" viewBox="0 0 50 46" fill="none" stroke="#fff" stroke-width="1.8"><circle cx="33" cy="13" r="6"/><circle cx="33" cy="13" r="2"/><path d="M33 4v3M33 19v3M24 13h3M39 13h3"/><path d="M6 24 18 14l12 10"/><path d="M9 22v18h18V22"/><rect x="14" y="30" width="8" height="10"/><path d="M4 42h42"/></svg></div>
  <h3>Maintenance Management</h3>
  <p>Lorem ipsum dolor sit amet, consectetur adipiscing elit, sed do eiusmod tempor incididunt ut labore et dolore.</p>
  <a class="btn">Read More</a>
</div>
<div class="abs service" style="left:801px;top:1777px">
  <div class="badge"><svg width="50" height="46" viewBox="0 0 50 46" fill="none" stroke="#fff" stroke-width="1.8"><circle cx="25" cy="30" r="7"/><path d="M25 26v8M23 27h3a1.5 1.5 0 0 1 0 3h-2a1.5 1.5 0 0 0 0 3h3"/><path d="M18 30H6M32 30h12M25 37v6M20 25l-8-8M30 25l8-8"/><path d="M16 20V10M22 20V6M28 20V8M34 20V4"/><circle cx="6" cy="30" r="2"/><circle cx="44" cy="30" r="2"/></svg></div>
  <h3>Financial Management</h3>
  <p>Lorem ipsum dolor sit amet, consectetur adipiscing elit, sed do eiusmod tempor incididunt ut labore et dolore.</p>
  <a class="btn">Read More</a>
</div>

<!-- Benefits -->
<section class="abs benefits"></section>
<svg class="abs benefits-notch" width="1200" height="80" viewBox="0 0 1200 80"><polygon points="0,0 1200,0 1200,2 600,78 0,2" fill="#f1eff2"/></svg>
<div class="abs benefits-photo" role="img" aria-label="Photo of three colleagues reviewing documents at a table in a bright office"></div>
<svg class="abs" style="left:560px;top:2196px" width="48" height="46" viewBox="0 0 48 46"><polygon points="24,0 29.6,17 47,17 33,27.5 38.4,45 24,34.5 9.6,45 15,27.5 1,17 18.4,17" fill="#c01d2e"/></svg>
<h2 class="abs heading benefits-title"><span class="light">Benefits of Professional</span><span class="bold">Property Management</span></h2>
<div class="abs rule benefits-rule"></div>
<p class="abs body-copy benefits-copy">Professional property management helps property owners reduce operational complexity while improving asset performance. Our structured management approach supports consistent maintenance, responsible financial oversight, tenant satisfaction, and efficient daily operations.</p>
<ul class="abs benefits-list">
  <li>Higher tenant retention</li>
  <li>Improved property condition</li>
  <li>Faster maintenance response</li>
  <li>Better operational efficiency</li>
  <li>Transparent financial reporting</li>
  <li>Reduced administrative workload</li>
  <li>Enhanced property value</li>
  <li>Long-term investment protection</li>
</ul>
<a class="abs btn benefits-cta">Read More</a>

<!-- Why choose -->
<h2 class="abs heading why-title"><span class="light">Why Choose</span><span class="bold">Our Property</span><span class="bold">Management</span><span class="light">Company</span></h2>
<ul class="abs why-list">
  <li><span class="dot"><svg width="16" height="16" viewBox="0 0 16 16" fill="none" stroke="#fff" stroke-width="1.4"><circle cx="8" cy="5" r="3"/><path d="M2 15c0-3.5 2.7-5 6-5s6 1.5 6 5"/></svg></span>Experienced Property Professionals</li>
  <li><span class="dot"><svg width="16" height="16" viewBox="0 0 16 16" fill="none" stroke="#fff" stroke-width="1.4"><path d="M2 3h12v8H6l-4 3z"/></svg></span>Transparent Communication</li>
  <li><span class="dot"><svg width="16" height="16" viewBox="0 0 16 16" fill="none" stroke="#fff" stroke-width="1.4"><circle cx="8" cy="8" r="2.5"/><path d="M8 1v3M8 12v3M1 8h3M12 8h3M3 3l2 2M11 11l2 2M3 13l2-2M11 5l2-2"/></svg></span>Efficient Operations</li>
  <li><span class="dot"><svg width="16" height="16" viewBox="0 0 16 16" fill="none" stroke="#fff" stroke-width="1.4"><path d="M3 1h8l2 2v12H3z"/><path d="M6 6h5M6 9h5M6 12h3"/></svg></span>Customized Management Plans</li>
  <li><span class="dot"><svg width="16" height="16" viewBox="0 0 16 16" fill="none" stroke="#fff" stroke-width="1.4"><circle cx="8" cy="4" r="2.2"/><circle cx="3" cy="12" r="2"/><circle cx="13" cy="12" r="2"/><path d="M8 6v3M8 9l-4 2M8 9l4 2"/></svg></span>Reliable Vendor Network</li>
  <li><span class="dot"><svg width="16" height="16" viewBox="0 0 16 16" fill="none" stroke="#fff" stroke-width="1.4"><path d="M2 14h12M4 12V8M8 12V5M12 12V2"/></svg></span>Focus on Long-Term Value</li>
</ul>
<a class="abs btn why-cta">Request a Consultation</a>
<svg class="abs" style="left:534px;top:2834px" width="48" height="46" viewBox="0 0 48 46"><polygon points="24,0 29.6,17 47,17 33,27.5 38.4,45 24,34.5 9.6,45 15,27.5 1,17 18.4,17" fill="#c01d2e"/></svg>
<div class="abs why-photo" role="img" aria-label="Photo of three business professionals reviewing a document together against a light wall"></div>

<!-- Delivering -->
<section class="abs delivering"></section>
<div class="abs delivering-photo" role="img" aria-label="Photo of a property manager guiding two clients through a bright home entrance"></div>
<h2 class="abs heading delivering-title"><span class="light">Delivering Exceptional</span><span class="bold">Property Management</span></h2>
<div class="abs rule delivering-rule"></div>
<p class="abs body-copy delivering-copy">We are the industry leaders in on-site management; able to better deliver exceptional property management services tailored to the distinct needs of Condominiums, Cooperatives, Homeowner Associations, New Development properties, Commercial spaces, and Multifamily communities. Our dedicated team is well-versed in all legal, financial, and operational aspects of property management, ensuring comprehensive support that aligns with the highest industry standards.</p>
<a class="abs btn delivering-cta">How We Serve You</a>

<!-- Contact -->
<h2 class="abs heading contact-title">
  <span class="line w-light">Looking For</span>
  <span class="line w-bold">Professional Property</span>
  <span class="line"><span class="w-bold">Management</span> <span class="w-light">Solutions?</span></span>
</h2>
<div class="abs rule contact-rule"></div>
<p class="abs body-copy contact-copy">Partner with an experienced property management team dedicated to protecting your investment, improving operational performance, and delivering exceptional tenant experiences.</p>
<a class="abs btn contact-cta">Contact Us</a>
<div class="abs hatch" style="left:1002px;top:4012px"></div>
<div class="abs hatch" style="left:592px;top:4442px"></div>
<form class="abs form-box">
  <div class="field" style="top:28px">Full Name</div>
  <div class="field" style="top:83px">Email</div>
  <div class="field" style="top:138px">Phone</div>
  <div class="field" style="top:195px;height:124px">Message</div>
  <a class="btn submit">Submit</a>
</form>
<svg class="abs" style="left:582px;top:4010px" width="48" height="46" viewBox="0 0 48 46"><polygon points="24,0 29.6,17 47,17 33,27.5 38.4,45 24,34.5 9.6,45 15,27.5 1,17 18.4,17" fill="#c01d2e"/></svg>

<!-- Footer -->
<footer class="abs site-footer"></footer>
<div class="abs footer-brand"><span>Larkfield<br>Ridge<br>Management</span></div>

<div class="abs foot-col" style="left:411px;top:4573px">
  <div class="foot-h">Contact Us</div>
  <div style="margin-top:22px">
    <div class="contact-row"><svg width="14" height="16" viewBox="0 0 14 16"><path d="M7 0a6 6 0 0 1 6 6c0 4.5-6 10-6 10S1 10.5 1 6a6 6 0 0 1 6-6z" fill="#c01d2e"/><circle cx="7" cy="6" r="2.2" fill="#efeef0"/></svg><span>1420 Alder Creek Rd, Ste 4,<br>Millbrook, WY 82990 USA</span></div>
    <div class="contact-row"><svg width="14" height="14" viewBox="0 0 24 24"><path d="M5 3h4l2 5-2.5 1.5a11 11 0 0 0 6 6L16 13l5 2v4a2 2 0 0 1-2 2A17 17 0 0 1 3 5a2 2 0 0 1 2-2z" fill="#c01d2e"/></svg><span>+1 555 014 2270</span></div>
    <div class="contact-row"><svg width="14" height="12" viewBox="0 0 14 12"><rect width="14" height="12" rx="1" fill="#c01d2e"/><path d="M1 1l6 5 6-5" fill="none" stroke="#efeef0" stroke-width="1.3"/></svg><span>info@larkfieldridge.com</span></div>
  </div>
</div>
<div class="abs foot-col" style="left:694px;top:4573px">
  <div class="foot-h">Menu</div>
  <ul><li>Home</li><li>About Us</li><li>Services</li><li>Industries</li><li>Resources</li><li>Contact Us</li></ul>
</div>
<div class="abs foot-col" style="left:852px;top:4573px">
  <div class="foot-h">Services</div>
  <ul><li>Residential Property Management</li><li>Commercial Property Management</li><li>Tenant Management</li><li>Lease Administration</li><li>Property Maintenance</li><li>Financial Management</li><li>Compliance &amp; Risk Management</li><li>Vendor Management</li></ul>
</div>
<div class="abs footer-rule"></div>
<div class="abs follow"><b>FOLLOW</b><i></i><i></i><i></i><i></i><i></i></div>
<div class="abs copyright">Copyright © 2026 All Rights Reserved</div>

</body>
</html>
```